Birchline Septic Solutions

Would like to see some single sided ones but would also like to see some double sided with one sided only being the logo. Owners name is Colin Vandro. Phone number is 555-214-0387
Services are pumping, inspections, installs, and repairs

Contact Information for Business Card

555-241-0387 Colin Vandro Larkridge, OH

```html
<!DOCTYPE html>
<html lang="en">
<head>
<meta charset="utf-8">
<title>Birchline Septic Solutions – Business Cards</title>
<link rel="stylesheet" href="https://fonts.googleapis.com/css2?family=Open+Sans:wght@400;600;700;800&display=swap">
<style>
  :root {
    --stage: #232323;
    --teal: #27bfb9;
    --teal-deep: #1f7f7c;
    --card-dark: #222226;
    --ink-white: #ffffff;
    --ridge-dark: #111114;
    --ridge-light: #2c2c31;
  }
  * { box-sizing: border-box; margin: 0; padding: 0; }
  html, body {
    width: 1200px; height: 779px; overflow: hidden;
    background: var(--stage);
    font-family: "Open Sans", Arial, sans-serif;
  }
  .canvas {
    width: 1200px; height: 779px;
    display: flex; align-items: center; justify-content: center; gap: 40px;
  }
  .card {
    position: relative;
    width: 540px; height: 309px;
    border-radius: 4px;
    overflow: hidden;
    box-shadow: 0 14px 30px rgba(0,0,0,.45);
  }

  /* Front: logo only */
  .card--front {
    background: var(--teal);
    display: flex; align-items: center; justify-content: center;
  }
  .brand-mark {
    display: flex; align-items: center; gap: 14px;
    color: var(--teal-deep);
    font-weight: 800;
  }
  .brand-mark__dot {
    width: 18px; height: 18px; border-radius: 50%;
    background: var(--teal-deep);
    flex: none;
  }
  .brand-mark__name {
    font-size: 48px; line-height: 1; letter-spacing: 1px;
    text-transform: uppercase;
  }
  .brand-mark__tag {
    display: block; font-size: 18px; letter-spacing: 6px; margin-top: 8px;
  }

  /* Back: contact side */
  .card--back { background: var(--card-dark); }
  .ridge-art {
    position: absolute; left: 0; top: 0; bottom: 0; width: 150px;
    background: linear-gradient(160deg, var(--ridge-light) 0%, var(--ridge-dark) 55%, var(--card-dark) 100%);
    clip-path: polygon(0 0, 45% 0, 70% 40%, 100% 62%, 80% 100%, 0 100%);
  }
  .back-brand {
    position: absolute; right: 58px; top: 30px;
    color: var(--ink-white); font-weight: 800; text-transform: uppercase;
    text-align: right; line-height: 1;
  }
  .back-brand__name { display: block; font-size: 36px; letter-spacing: 1px; }
  .back-brand__tag { display: block; font-size: 12px; letter-spacing: 5px; margin-top: 6px; }
  .accent-bar {
    position: absolute; right: 34px; top: 112px;
    width: 8px; height: 64px; background: var(--teal);
  }
  .contact {
    position: absolute; right: 58px; top: 108px;
    text-align: right; color: var(--ink-white);
  }
  .contact__name { font-size: 24px; font-weight: 700; line-height: 1.15; }
  .contact__first { color: var(--teal); }
  .contact__line { font-size: 13px; font-weight: 600; line-height: 1.5; }
  .contact__phone { display: inline-flex; align-items: center; gap: 6px; }
  .contact__phone svg { width: 12px; height: 12px; fill: var(--teal); }

  .services {
    position: absolute; left: 150px; right: 30px; bottom: 34px;
    color: var(--ink-white);
  }
  .services__label {
    display: inline-block;
    background: var(--teal); color: var(--ink-white);
    font-size: 12px; font-weight: 600; letter-spacing: .5px;
    padding: 3px 14px; border-radius: 50%/50%;
    margin-left: 120px; margin-bottom: 8px;
  }
  .services__list {
    list-style: none; display: flex; gap: 12px; flex-wrap: nowrap;
    font-size: 14px;
  }
  .services__list li { display: flex; align-items: center; gap: 6px; white-space: nowrap; }
  .services__list li::before {
    content: ""; width: 8px; height: 8px; border-radius: 50%; background: var(--teal);
  }
</style>
</head>
<body>
<main class="canvas">
  <section class="card card--front" aria-label="Card front">
    <div class="brand-mark">
      <span class="brand-mark__dot"></span>
      <span class="brand-mark__name">Birchline<span class="brand-mark__tag">Septic Solutions</span></span>
    </div>
  </section>

  <section class="card card--back" aria-label="Card back">
    <div class="ridge-art" role="img" aria-label="Dark mountain ridge and pine tree silhouette along the left edge"></div>

    <div class="back-brand">
      <span class="back-brand__name">Birchline</span>
      <span class="back-brand__tag">Septic Solutions</span>
    </div>

    <div class="accent-bar"></div>

    <div class="contact">
      <p class="contact__name"><span class="contact__first">Colin</span> Vandro</p>
      <p class="contact__line">Larkridge, OH</p>
      <p class="contact__line contact__phone">555-241-0387
        <svg viewBox="0 0 24 24" aria-hidden="true"><path d="M6.6 10.8a15.1 15.1 0 0 0 6.6 6.6l2.2-2.2a1 1 0 0 1 1-.25 11.4 11.4 0 0 0 3.6.57 1 1 0 0 1 1 1V20a1 1 0 0 1-1 1A17 17 0 0 1 3 4a1 1 0 0 1 1-1h3.5a1 1 0 0 1 1 1c0 1.25.2 2.45.57 3.57a1 1 0 0 1-.25 1z"/></svg>
      </p>
    </div>

    <div class="services">
      <span class="services__label">SERVICES</span>
      <ul class="services__list">
        <li>Pumping</li>
        <li>Inspections</li>
        <li>Installs</li>
        <li>And Repairs</li>
      </ul>
    </div>
  </section>
</main>
</body>
</html>
```